Coastal Learner Bureau business cards

Australian company about to start offering its services. We recruit international students to come to study English, vocational education and postgraduate courses in Australia. We help them find the institution and select the right city they want to come to Australia. We are a young, online oriented and supportive agency. Our clients are between 18 and 35 years old, mainly University students, young professionals or people with work experience. We provide much more information that any other agency offer. We administrate a Facebook group with more than 11.000 members that daily ask questions about general information when coming to Australia, while they are here and even after they leave the country

Target Market(s)

International students from South America, Central America and Europe

Industry/Entity Type

Student

Contact Information for Business Card

Tomas Bilbrea
Managing Director
tomas@kelvarin.com.au
www.kelvoria.com.au
+61 491058264
Melbourne, Australia

Font styles to use
Serif
Sans Serif

Colors

Designer to choose colors to be used in the design.

Requirements
Must have
• Horizontal design
• Standard business card size and shape. If font uses green or yellow colours, they will have to match the ones from the logo
Nice to have
• UPDATE: Use the contents of the green image to design one of the card sides. Use our logo in the background of that side as watermark.
• Passport image, or immigration stamps. A picture of the Yarra River (from Melbourne) would be cool as well.
Should not have
• Non-standard business card size and shape
• Not black as the background colour of any sides as we are not a VIP agency or a hight class service. We are orientes to young people and they like colours, pictures, something attractive.
• Vertical design
• NO YELLOW or BLACK AS THE BACKGROUND COLOUR OF ANY SIDE OF THE BIZ CARD

```html
<!DOCTYPE html>
<html lang="en">
<head>
<meta charset="utf-8">
<title>Coastal Learner Bureau – Business Cards</title>
<link rel="stylesheet" href="https://fonts.googleapis.com/css2?family=Roboto:wght@400;500&family=Roboto+Condensed:wght@700&display=swap">
<style>
  :root {
    --backdrop: #2a2a2a;
    --paper: #f2f2f2;
    --brand-green: #155a3a;
    --brand-yellow: #dfb515;
    --ink: #444444;
    --rule: #8a8a8a;
    --white: #ffffff;
  }
  * { margin: 0; padding: 0; box-sizing: border-box; }
  html, body {
    width: 1200px; height: 960px; overflow: hidden;
    background: var(--backdrop);
    font-family: "Roboto", Arial, sans-serif;
  }
  .stage { position: relative; width: 1200px; height: 960px; }
  .card { position: absolute; width: 600px; height: 343px; overflow: hidden; }

  /* Front side */
  .card--front { left: 314px; top: 113px; background: var(--paper); }
  .brand-name {
    font-family: "Roboto Condensed", "Arial Narrow", sans-serif;
    font-weight: 700; color: var(--brand-green);
    position: absolute; white-space: nowrap;
  }
  .card--front .brand-name { right: 37px; top: 80px; font-size: 52px; line-height: 1; }
  .person-name {
    position: absolute; left: 38px; top: 193px;
    font-family: "Roboto Condensed", "Arial Narrow", sans-serif;
    font-weight: 700; font-size: 23px; color: var(--brand-green); letter-spacing: 0.2px;
  }
  .person-title {
    position: absolute; left: 38px; top: 218px;
    font-size: 16px; font-weight: 500; color: var(--brand-yellow); letter-spacing: 0.3px;
  }
  .divider { position: absolute; left: 38px; top: 243px; width: 525px; height: 1px; background: var(--rule); }
  .contact-list { position: absolute; left: 38px; top: 256px; list-style: none; }
  .contact-item {
    display: flex; align-items: center; gap: 7px;
    font-size: 15px; color: var(--ink); height: 19px;
  }
  .contact-item svg { width: 14px; height: 14px; fill: var(--brand-green); }
  .location {
    position: absolute; right: 37px; top: 272px;
    font-size: 15px; color: var(--ink);
  }
  .bands { position: absolute; left: 0; top: 0; width: 600px; height: 343px; }
  .website {
    position: absolute; left: 405px; top: 316px;
    font-size: 15px; color: var(--white);
  }

  /* Back side */
  .card--back { left: 311px; top: 472px; background: var(--brand-green); }
  .card--back .brand-name {
    left: 0; right: 0; top: 130px; text-align: center;
    font-size: 72px; line-height: 1; color: var(--white);
  }
  .tagline {
    position: absolute; left: 0; right: 0; top: 300px;
    display: flex; align-items: center; justify-content: center; gap: 4px;
    font-size: 15px; color: var(--white);
  }
  .tagline::before, .tagline::after {
    content: ""; height: 1px; width: 145px;
  }
  .tagline::before { background: linear-gradient(to right, rgba(255,255,255,0), var(--brand-yellow)); }
  .tagline::after { background: linear-gradient(to left, rgba(255,255,255,0), var(--brand-yellow)); }
</style>
</head>
<body>
<main class="stage">

  <section class="card card--front" aria-label="Business card front">
    <div class="brand-name">Kelvoria</div>

    <h1 class="person-name">TOMAS BILBREA</h1>
    <p class="person-title">MANAGING DIRECTOR</p>
    <div class="divider"></div>

    <ul class="contact-list">
      <li class="contact-item">
        <svg viewBox="0 0 24 24" aria-hidden="true"><path d="M6.6 10.8a15.1 15.1 0 0 0 6.6 6.6l2.2-2.2c.3-.3.7-.4 1-.2 1.1.4 2.3.6 3.6.6.6 0 1 .4 1 1V20c0 .6-.4 1-1 1A17 17 0 0 1 3 4c0-.6.4-1 1-1h3.5c.6 0 1 .4 1 1 0 1.3.2 2.5.6 3.6.1.3 0 .7-.2 1z"/></svg>
        +61 491058264
      </li>
      <li class="contact-item">
        <svg viewBox="0 0 24 24" aria-hidden="true"><path d="M2 5h20v14H2z" fill="var(--brand-green)"/><path d="M3 6.5l9 6.5 9-6.5" fill="none" stroke="#f2f2f2" stroke-width="1.6"/></svg>
        tomas@kelvarin.com.au
      </li>
    </ul>

    <p class="location">Melbourne, Australia</p>

    <svg class="bands" viewBox="0 0 600 343" aria-hidden="true">
      <polygon points="0,320 347,320 339,330 0,330" fill="var(--brand-yellow)"/>
      <rect x="0" y="333" width="600" height="10" fill="var(--brand-green)"/>
      <polygon points="362,311 600,311 600,343 338,343" fill="var(--brand-green)"/>
    </svg>
    <p class="website">www.kelvoria.com.au</p>
  </section>

  <section class="card card--back" aria-label="Business card back">
    <div class="brand-name">Kelvoria</div>
    <p class="tagline">Hacemos más por ti!</p>
  </section>

</main>
</body>
</html>
```